Casa Morellina Togo Menu seperated in categories

new to go menu for italian restaurant with menu descriptions and prices i like the cover first page to have all the restaurant information, the other pages should be separated in the menu categories, and if we can include a map with the location of the restaurant
Casa Morellina
42 Route 83 S
North Myrtle Beach, SC 29582
open 7 days a week 4-10
Happy hour served Daily at the Bar 4-7
www.casamorellina.com
casamorellinadine@maildrop.example

Restaurant

Sans Serif

Must have
• Prices and pictures and restaurant information

```html
<!DOCTYPE html>
<html lang="en">
<head>
<meta charset="utf-8">
<title>Casa Morellina – Seafood</title>
<link href="https://fonts.googleapis.com/css2?family=Oswald:wght@400;500&family=Open+Sans:wght@400&display=swap" rel="stylesheet">
<style>
  :root {
    --frame-red: #a3232f;
    --price-red: #9b1c2a;
    --ink: #1a1a1a;
    --paper: #ffffff;
    --photo-dark: #2e1a12;
    --photo-warm: #7a4a2c;
  }
  * { margin: 0; padding: 0; box-sizing: border-box; }
  html, body { width: 667px; height: 1200px; overflow: hidden; background: var(--paper); }
  .menu-page {
    position: relative; width: 667px; height: 1200px; background: var(--paper);
    font-family: "Open Sans", Arial, sans-serif; color: var(--ink);
  }
  .page-frame {
    position: absolute; left: 40px; top: 40px; width: 589px; height: 1123px;
    border: 2px solid var(--frame-red);
  }
  .section-title {
    position: absolute; left: 71px; top: 96px;
    font-family: "Oswald", Arial, sans-serif; font-weight: 500;
    font-size: 64px; line-height: 1; letter-spacing: -0.5px; color: #111;
  }
  .section-intro {
    position: absolute; left: 72px; top: 181px; width: 540px;
    font-size: 13.6px; line-height: 18px; white-space: nowrap;
  }
  .upgrade-note, .split-note {
    position: absolute; font-size: 11px; line-height: 14px; display: flex; align-items: center; gap: 8px;
  }
  .upgrade-note { left: 232px; top: 246px; }
  .split-note { left: 418px; top: 233px; }
  .note-price {
    font-family: "Oswald", Arial, sans-serif; font-size: 15px; color: var(--price-red); letter-spacing: -0.5px;
  }
  .dish-list { position: absolute; left: 71px; top: 308px; width: 518px; list-style: none; }
  .dish { height: 82px; }
  .dish-head { display: flex; align-items: baseline; height: 26px; }
  .dish-name {
    font-family: "Oswald", Arial, sans-serif; font-size: 19px; font-weight: 400; white-space: nowrap;
  }
  .dish-leader {
    flex: 1; margin: 0 4px 0 8px; border-bottom: 1px dashed var(--price-red); transform: translateY(-6px);
  }
  .dish-price {
    font-family: "Oswald", Arial, sans-serif; font-size: 19px; color: var(--price-red); letter-spacing: -0.3px;
  }
  .dish-desc { font-size: 13.6px; line-height: 18px; white-space: nowrap; }
  .dish-photo {
    position: absolute; left: 41px; top: 768px; width: 587px; height: 394px;
    background: linear-gradient(180deg, var(--photo-dark) 0%, var(--photo-warm) 100%);
  }
</style>
</head>
<body>
<main class="menu-page">
  <div class="page-frame"></div>
  <h1 class="section-title">SEAFOOD</h1>
  <p class="section-intro">All of our Seafood Dishes served with fresh baked bread and our roasted red<br>pepper, garlic and herb dipping oil, your choice of soup of the day or house<br>salad,</p>
  <p class="upgrade-note"><span>Upgrade to Caesar Salad</span><span class="note-price">1,95</span></p>
  <p class="split-note"><span>Split Entrée includes<br>additional soup or salad</span><span class="note-price">7,00</span></p>

  <ul class="dish-list">
    <li class="dish">
      <div class="dish-head"><span class="dish-name">Linguini With Clams Sauce</span><span class="dish-leader"></span><span class="dish-price">18.95</span></div>
      <p class="dish-desc">Fresh little neck Clams sautéed in extra virgin oil, Garlic chunks and baby<br>Clams in their own juice, served over linguini in a Red or White sauce</p>
    </li>
    <li class="dish">
      <div class="dish-head"><span class="dish-name">Spaghetti With Mussels</span><span class="dish-leader"></span><span class="dish-price">18.95</span></div>
      <p class="dish-desc">Fresh PEI Mussels sautéed with your choice of Marinara, Scampi or Fra Diavolo<br>sauce, served over spaghetti</p>
    </li>
    <li class="dish">
      <div class="dish-head"><span class="dish-name">Shrimp &amp; Scallops</span><span class="dish-leader"></span><span class="dish-price">24.95</span></div>
      <p class="dish-desc">Choice of Shrimp or fresh Sea Scallops or Combo, sautéed in your choice of<br>Marinara, Scampi or Fra Diavolo sauce, served over linguini</p>
    </li>
    <li class="dish">
      <div class="dish-head"><span class="dish-name">Grouper Florentine</span><span class="dish-leader"></span><span class="dish-price">25.95</span></div>
      <p class="dish-desc">Fresh Grouper egg battered, finished in a lemon chardonnay butter sauce, and<br>served over spinach and linguini</p>
    </li>
    <li class="dish">
      <div class="dish-head"><span class="dish-name">Zuppa Di Pesce</span><span class="dish-leader"></span><span class="dish-price">28.95</span></div>
      <p class="dish-desc">Shrimp, Sea Scallops, Calamari, PEI Mussels, Little Neck Clams and Grouper,<br>sautéed in your choice of Marinara or Fra Diavolo sauce, served over linguini</p>
    </li>
  </ul>

  <div class="dish-photo" role="img" aria-label="Photo of a seafood linguini plate with garlic bread and a glass of white wine on a wooden table"></div>
</main>
</body>
</html>
```